Business Card Design for Training Business

Clear Path Coaching is a new business that delivers training and other services with a focus on topics related to mental health and wellbeing, for example, Wellmind Response Course, Resilience etc. We have a strong focus on evidence-based psychology and neuroscience. I have a logo which I will upload with the brief, so please consider colours that work well with the logo.
Target Market(s)
Adults, workplaces (particularly government and not-for-profits)
Industry/Entity Type
Business
Contact Information for Business Card
Head Strong TrainingSamantha SellwoodDirector0438 770 850sam@headstrongtraining.com.auwww.headstrongtraining.com.au

```html
<!DOCTYPE html>
<html lang="en">
<head>
<meta charset="utf-8">
<title>Clear Path Coaching – Business Card</title>
<link rel="stylesheet" href="https://fonts.googleapis.com/css2?family=Arimo:wght@400&display=swap">
<style>
  :root {
    --backdrop: #8f8f8f;
    --card: #f4f4f4;
    --card-edge: #e6e6e6;
    --teal: #1aa8b4;
    --teal-soft: #8fd3cf;
    --ink: #4a3b36;
    --brand-ink: #5b4d48;
  }
  * { margin: 0; padding: 0; box-sizing: border-box; }
  html, body {
    width: 1200px; height: 965px; overflow: hidden;
    background: var(--backdrop);
    font-family: "Arimo", Arial, sans-serif;
  }
  .canvas { position: relative; width: 1200px; height: 965px; }
  .card {
    position: absolute; left: 98px; top: 198px;
    width: 1004px; height: 568px;
    background: radial-gradient(ellipse at 45% 50%, #ffffff 0%, var(--card) 60%, var(--card-edge) 100%);
    overflow: hidden;
  }
  .brand { position: absolute; left: 49px; top: 48px; width: 325px; text-align: center; color: var(--brand-ink); }
  .brand-mark {
    display: block; width: 134px; height: 134px; margin: 0 auto 30px;
    border: 2px solid var(--teal); border-radius: 50%;
  }
  .brand-name { font-size: 35px; letter-spacing: 3px; line-height: 1; white-space: nowrap; }
  .brand-sub { font-size: 18px; letter-spacing: 6px; margin-top: 14px; }
  .person { position: absolute; left: 50px; top: 344px; }
  .person-name { font-size: 28px; color: var(--teal); line-height: 1.2; }
  .person-role { font-size: 21px; color: var(--ink); margin-top: 4px; }
  .contacts { position: absolute; left: 50px; top: 440px; list-style: none; }
  .contact { display: flex; align-items: center; height: 29px; font-size: 21px; color: var(--ink); }
  .contact-icon { width: 22px; height: 22px; margin-right: 16px; fill: var(--teal); }
  .decoration {
    position: absolute; right: 0; top: 0; width: 284px; height: 568px;
    background: linear-gradient(90deg, rgba(26,168,180,0) 0%, rgba(143,211,207,0.35) 55%, rgba(26,168,180,0.45) 100%);
  }
</style>
</head>
<body>
<div class="canvas">
  <section class="card">
    <div class="brand">
      <span class="brand-mark"></span>
      <div class="brand-name">CLEAR PATH</div>
      <div class="brand-sub">COACHING</div>
    </div>

    <div class="person">
      <div class="person-name">Rebecca Tanfield</div>
      <div class="person-role">Director</div>
    </div>

    <ul class="contacts">
      <li class="contact">
        <svg class="contact-icon" viewBox="0 0 24 24"><path d="M6.6 10.8a15.1 15.1 0 0 0 6.6 6.6l2.2-2.2a1 1 0 0 1 1-.25 11.4 11.4 0 0 0 3.6.57 1 1 0 0 1 1 1V20a1 1 0 0 1-1 1A17 17 0 0 1 3 4a1 1 0 0 1 1-1h3.5a1 1 0 0 1 1 1c0 1.25.2 2.45.57 3.6a1 1 0 0 1-.25 1z"/></svg>
        0491 362 517
      </li>
      <li class="contact">
        <svg class="contact-icon" viewBox="0 0 24 24"><path d="M2 5h20v14H2z M3.5 6.5 12 13l8.5-6.5" fill="var(--teal)" stroke="#fff" stroke-width="1.4"/></svg>
        bec@clearpathcoaching.example.au
      </li>
      <li class="contact">
        <svg class="contact-icon" viewBox="0 0 24 24" fill="none" stroke="var(--teal)" stroke-width="1.8"><circle cx="12" cy="12" r="9.5"/><ellipse cx="12" cy="12" rx="4" ry="9.5"/><path d="M2.5 12h19M4 7h16M4 17h16"/></svg>
        www.clearpathcoaching.example.au
      </li>
    </ul>

    <div class="decoration" role="img" aria-label="Large decorative brand motif in teal at the right edge of the card"></div>
  </section>
</div>
</body>
</html>
```